VENTURE CAPITAL GROUP BUSINESS CARD DESIGN

Venture Capital Group based in SF looking for a bold business card design. No trendy colour explosion, 3D effects etc. Just "simple" optical effects. Works on your brain, keeps your eye focused and sticks to your mind.
Target Market(s)
Technology startups
Industry/Entity Type
Venture Capital
Contact Information for Business Card
DESMOND WHITLAKE
MANAGING PARTNER
187 FENWORTH ST SAN FRANCISCO, CA 94187
415.555.0142 O
415.555.0147 F
415.555.0193 C
desmond@veldtmoorcapital.ventures

```html
<!DOCTYPE html>
<html lang="en">
<head>
<meta charset="utf-8">
<title>Veldtmoor Capital Group – Business Card</title>
<link rel="stylesheet" href="https://fonts.googleapis.com/css2?family=Open+Sans:wght@400;600;700;800&display=swap">
<style>
  :root{
    --backdrop:#2b2b2d;
    --card:#ffffff;
    --green-deep:#0f5a27;
    --green-mid:#1d7a34;
    --green-bright:#3fb54a;
    --ink:#1f3d26;
    --silver:#d9dadb;
    --white:#ffffff;
  }
  *{margin:0;padding:0;box-sizing:border-box}
  html,body{width:1200px;height:900px;overflow:hidden;background:var(--backdrop)}
  body{font-family:"Open Sans",Arial,sans-serif;position:relative}

  .card{
    position:absolute;width:640px;height:365px;background:var(--card);
    border-radius:26px;overflow:hidden;
  }
  .card--front{left:280px;top:60px}
  .card--back{left:280px;top:475px}

  /* front */
  .front-mark{
    position:absolute;left:50%;top:70px;width:120px;height:120px;margin-left:-60px;
    border-radius:50%;background:var(--silver);
  }
  .front-name{
    position:absolute;left:0;right:0;top:215px;text-align:center;
    color:var(--green-mid);font-weight:600;font-size:30px;letter-spacing:1px;line-height:1.15;
  }
  .front-name span{display:block;font-size:15px;letter-spacing:6px}

  /* back */
  .back-art{position:absolute;inset:0}
  .back-mark{
    position:absolute;right:30px;top:-8px;width:118px;height:118px;border-radius:50%;
    background:var(--silver);
  }
  .back-company{
    position:absolute;left:40px;top:72px;color:var(--green-mid);
    font-weight:600;font-size:26px;letter-spacing:1px;line-height:1.15;
  }
  .back-company span{display:block;font-size:12px;letter-spacing:5px}
  .holder{position:absolute;left:40px;top:175px}
  .holder-name{font-weight:800;font-size:23px;color:var(--ink);letter-spacing:.5px}
  .holder-role{font-weight:700;font-size:14px;color:var(--green-bright);letter-spacing:.5px;margin-top:-2px}
  .holder-address{font-weight:600;font-size:14px;color:var(--ink);margin-top:12px;line-height:1.3}

  .contact-list{position:absolute;right:26px;top:178px;list-style:none;text-align:right}
  .contact-list li{
    color:var(--white);font-weight:600;font-size:14px;line-height:21px;
    display:flex;justify-content:flex-end;align-items:center;gap:8px;
  }
  .contact-list svg{width:12px;height:12px;fill:none;stroke:var(--green-bright);stroke-width:1.6}
  .contact-email{
    position:absolute;right:26px;bottom:48px;color:var(--white);
    font-weight:600;font-size:15px;letter-spacing:.2px;
  }
</style>
</head>
<body>

<section class="card card--front" aria-label="Card front">
  <div class="front-mark"></div>
  <div class="front-name">VELDTMOOR<span>CAPITAL GROUP</span></div>
</section>

<section class="card card--back" aria-label="Card back">
  <svg class="back-art" viewBox="0 0 640 365" preserveAspectRatio="none" aria-hidden="true">
    <path d="M640 0 L560 0 C480 70 470 160 420 225 C370 290 270 330 180 365 L640 365 Z" fill="var(--green-deep)"/>
    <path d="M548 0 C468 70 458 160 408 225 C358 290 258 330 168 365" fill="none" stroke="var(--green-bright)" stroke-width="4"/>
    <path d="M0 365 L0 330 C80 320 170 335 250 340 C200 352 160 360 150 365 Z" fill="var(--green-bright)"/>
    <path d="M0 318 C90 308 190 325 260 330" fill="none" stroke="var(--green-deep)" stroke-width="4"/>
    <rect x="500" y="38" width="140" height="10" fill="var(--green-bright)"/>
  </svg>
  <div class="back-mark"></div>

  <div class="back-company">VELDTMOOR<span>CAPITAL GROUP</span></div>

  <div class="holder">
    <div class="holder-name">DESMOND WHITLAKE</div>
    <div class="holder-role">MANAGING PARTNER</div>
    <div class="holder-address">187 FENWORTH ST SAN<br>FRANCISCO, CA 94187</div>
  </div>

  <ul class="contact-list">
    <li>415.555.0142
      <svg viewBox="0 0 12 12"><path d="M2 1.5 L4 1.5 L5 4 L3.8 5 C4.5 6.5 5.5 7.5 7 8.2 L8 7 L10.5 8 L10.5 10 C6 10.5 1.5 6 2 1.5 Z"/></svg></li>
    <li>415.555.0147
      <svg viewBox="0 0 12 12"><rect x="1.5" y="4.5" width="9" height="4.5"/><rect x="3.5" y="1.5" width="5" height="3"/><rect x="3.5" y="7.5" width="5" height="3"/></svg></li>
    <li>415.555.0193
      <svg viewBox="0 0 12 12"><rect x="3" y="1" width="6" height="10" rx="1"/><path d="M5.5 9.3 H6.5"/></svg></li>
    <li>&nbsp;
      <svg viewBox="0 0 12 12"><rect x="1.5" y="3" width="9" height="6.5"/><path d="M1.5 3 L6 7 L10.5 3"/></svg></li>
  </ul>
  <div class="contact-email">desmond@veldtmoorcapital.ventures</div>
</section>

</body>
</html>
```